Wordpress design for media production company

We are a small production company called Copper Lantern Films specializing in documentary and short film.

We are after a wordpress web site that is fun and engaging with a relaxed feel. We would like to be able to easily edit and maintain the website ourselves.

We would like:
* A title screen that has a photo taking up most of the screen.
* Contact details (inc. social media links) on a static bar at the bottom.
* An area for our previous work. Some thumbnails or icons that open up and embedded youtube or vimeo video.
* An area for "about us" which will have information on the company and links to separate profiles of 3 (initially) employees.
* A Blog.
* Somewhere to show what we are currently working on.
* Examples of other stuff we have done (ie. photography, poetry, audio, animation and VFX).

We already have a logo that can be animated. It would be very cool to have it as a "Loading" page while things load in the background.

The text needs to be fun but easy to read.

We already have a license for "Q Layout" which seems pretty cool and flexible, so if you wanted to use it then great but if not then that is fine too.

A couple of pages that we like are:
http://www.plumorchardworks.com/
http://dorianvelkot.com/
http://www.spinthegrove.com/

Please do not hesitate to contact me if you would like more information on anything.

Cheers

Gideon

Target Market(s)

Mainly Australian clients seeking media services
Broadcasting companies

Industry/Entity Type

It Company

Requirements
Nice to have
• I love the parallax look on http://www.plumorchardworks.com/

```html
<!DOCTYPE html>
<html lang="en">
<head>
<meta charset="utf-8">
<title>Copper Lantern Films</title>
<link href="https://fonts.googleapis.com/css2?family=Open+Sans:wght@400;600;700&family=PT+Sans:wght@700&display=swap" rel="stylesheet">
<style>
:root{
  --red:#b30000;
  --red-bright:#c40d0d;
  --black:#000;
  --footer-dark:#0d0d0d;
  --ink:#222;
  --muted:#666;
  --line:#e2e2e2;
  --panel:#efefef;
  --white:#fff;
}
*{margin:0;padding:0;box-sizing:border-box}
html,body{width:1200px;height:2528px;overflow:hidden}
body{position:relative;background:var(--white);font-family:"Open Sans",Arial,sans-serif;color:var(--ink)}
.abs{position:absolute}
.ph{position:absolute}

/* header */
.site-header{position:absolute;left:0;top:0;width:1200px;height:81px;background:var(--black)}
.header-rule{position:absolute;left:0;top:81px;width:1200px;height:4px;background:var(--red)}
.brand{position:absolute;left:214px;top:14px;display:flex;align-items:center;gap:8px}
.brand-mark{width:34px;height:34px;border-radius:50%;background:var(--white)}
.brand-name{color:var(--white);font-size:11px;font-weight:700}
.main-nav{position:absolute;top:34px;left:0;width:1200px;height:20px}
.main-nav a{position:absolute;color:var(--white);font-size:13px;text-decoration:none}

/* hero */
.hero{position:absolute;left:0;top:85px;width:1200px;height:491px;background:linear-gradient(180deg,#dfe4ea 0%,#c9d0d8 45%,#eef1f4 70%,#f6f7f9 100%)}
.hero-title{position:absolute;top:228px;width:1200px;text-align:center;font-family:"PT Sans",sans-serif;font-weight:700;font-size:30px;color:#111}
.hero-sub{position:absolute;top:271px;width:1200px;text-align:center;font-family:"PT Sans",sans-serif;font-weight:700;font-size:14px;color:#111}
.btn-more{position:absolute;left:539px;top:329px;width:121px;height:37px;background:var(--red-bright);color:var(--white);font-size:13px;font-weight:700;display:flex;align-items:center;justify-content:center;border-radius:2px}
.hero-dot{position:absolute;width:6px;height:6px;border-radius:50%;background:var(--red-bright)}
.hero-dot.active{width:18px;height:18px;border:2px solid #222;background:none}
.hero-dot.active::after{content:"";position:absolute;left:4px;top:4px;width:6px;height:6px;border-radius:50%;background:#222}

.section-title{position:absolute;color:var(--red-bright);font-weight:700;font-size:16px}
.small-text{font-size:9.5px;line-height:19px;color:#333}
.rule{position:absolute;height:1px;background:var(--line)}

/* blog */
.blog-avatar{position:absolute;left:200px;width:51px;height:51px;border-radius:50%;background:radial-gradient(circle,#e7c9a8,#5d8db8);border:2px solid #ddd}
.blog-text{position:absolute;left:266px;width:225px;font-size:9px;line-height:16px;color:#333}

/* videos */
.video-main{left:578px;top:913px;width:244px;height:213px;background:linear-gradient(160deg,#eef2f6,#a9b9c9 55%,#50606e)}
.video-bar{position:absolute;left:578px;top:1114px;width:244px;height:12px;background:#1a1a1a}
.video-thumb{left:832px;width:133px}
.play{position:absolute;width:22px;height:22px;border-radius:50%;background:rgba(40,40,40,.7)}
.play::after{content:"";position:absolute;left:8px;top:6px;border-left:8px solid #fff;border-top:5px solid transparent;border-bottom:5px solid transparent}
.view-more{position:absolute;left:836px;top:1110px;font-size:10px;color:var(--red-bright);text-decoration:underline}

/* tabs */
.tab{position:absolute;top:1193px;height:47px;background:#e6e6e6;color:#888;font-size:13px;font-weight:600;letter-spacing:.5px;display:flex;align-items:center;justify-content:center}
.tab.active{background:var(--panel);color:#222;border-top:3px solid var(--red-bright)}
.tab-panel{position:absolute;left:190px;top:1240px;width:819px;height:255px;background:var(--panel)}
.tab-heading{position:absolute;left:581px;top:1279px;font-size:18px;font-weight:600;letter-spacing:1px;color:#222}
.tab-copy{position:absolute;left:581px;top:1331px;width:395px;font-size:9.5px;line-height:20px;color:#333}
.readmore{position:absolute;left:580px;top:1444px;font-size:10.5px;color:var(--red-bright);display:flex;align-items:center;gap:6px}

/* projects */
.project{position:absolute;top:1597px;width:192px}
.project-img{height:189px;border-radius:3px}
.project-name{text-align:center;font-size:14.5px;margin-top:13px;color:#222}
.project-sub{text-align:center;font-size:10.5px;color:var(--muted)}

/* testimonials */
.testi-title{position:absolute;top:1938px;width:1200px;text-align:center;font-size:20px;color:#333}
.testi-title b{font-weight:700}
.testi-quote{position:absolute;left:205px;top:1995px;width:790px;text-align:center;font-size:15.5px;line-height:22px;color:#555}
.testi-name{position:absolute;top:2078px;width:1200px;text-align:center;font-size:12px;color:#555}
.testi-name b{color:#333}
.t-dot{position:absolute;top:2113px;width:7px;height:7px;border-radius:50%;background:#ddd}
.t-dot.active{background:var(--red-bright)}

/* footer */
.site-footer{position:absolute;left:0;top:2174px;width:1200px;height:281px;background:var(--red)}
.foot-col{position:absolute;top:2229px;color:var(--white)}
.foot-col h4{font-size:15.5px;font-weight:400;margin-bottom:14px}
.foot-col p{font-size:10.5px;line-height:18.5px}
.contact-row{display:flex;align-items:center;gap:12px;font-size:10.5px;margin-top:5px}
.tweet{display:flex;gap:10px;font-size:10.5px;line-height:18px}
.tweet-dot{flex:none;width:12px;height:12px;border-radius:50%;background:var(--white);margin-top:3px}
.email-field{position:absolute;left:849px;top:2325px;width:125px;height:27px;background:var(--white);font-size:10px;color:#aaa;padding:7px 10px}
.email-go{position:absolute;left:974px;top:2325px;width:35px;height:27px;background:#111;color:var(--white);font-size:11px;display:flex;align-items:center;justify-content:center}
.bottom-bar{position:absolute;left:0;top:2455px;width:1200px;height:73px;background:var(--footer-dark)}
.copyright{position:absolute;left:190px;top:2483px;font-size:10px;color:#ddd}
.social{position:absolute;top:2478px;width:24px;height:24px;border-radius:50%;background:var(--red-bright)}
</style>
</head>
<body>

<header class="site-header">
  <div class="brand"><span class="brand-mark"></span><span class="brand-name">Copper Lantern Films</span></div>
  <nav class="main-nav">
    <a style="left:602px">Home</a>
    <a style="left:662px">About us</a>
    <a style="left:743px">Services</a>
    <a style="left:824px">Blog</a>
    <a style="left:878px">News</a>
    <a style="left:937px">Contact</a>
  </nav>
</header>
<div class="header-rule"></div>

<section class="hero" role="img" aria-label="Snowy lakeside village with skaters on a frozen pond and frosted trees">
  <h1 class="hero-title" style="top:143px">Suspendisse mauris. Fusce accumsan mollis eros.</h1>
  <p class="hero-sub" style="top:186px">Pellentesque a diam sit amet mi ullamcorper vehicula. Integer adipiscing</p>
  <div class="btn-more" style="top:244px">SHOW MORE</div>
  <span class="hero-dot" style="left:568px;top:443px"></span>
  <span class="hero-dot active" style="left:591px;top:437px"></span>
  <span class="hero-dot" style="left:626px;top:443px"></span>
</section>

<h2 class="section-title" style="left:189px;top:603px">Welcome to Copper Lantern Films</h2>
<div class="ph" role="img" aria-label="Older couple riding bicycles outdoors" style="left:190px;top:652px;width:174px;height:123px;background:linear-gradient(135deg,#b9d8ee,#7fa9c9 50%,#88a86a)"></div>
<p class="abs small-text" style="left:391px;top:651px;width:615px">Morbi interdum mollis sapien. Sed ac risus. Phasellus lacinia, magna a ullamcorper laoreet, lectus arcu pulvinar risus, vitae facilisis libero dolor a purus. Sed vel lacus. Mauris nibh felis, adipiscing varius, adipiscing in, lacinia vel, tellus. Suspendisse ac urna. Etiam pellentesque mauris ut lectus. Nunc tellus ante, mattis eget, gravida vitae, ultricies ac, leo. Integer leo pedeMorbi interdum mollis sapien. Sed ac risus. Phasellus lacinia, magna a ullamcorper laoreet, lectus arcu pulvinar risus, vitae facilisis libero dolor a purus. Sed vel lacus. Mauris nibh felis, adipiscing varius, adipiscing in, lacinia vel, tellus. Suspendisse ac urna. leo pedeMorbi interdum mollis sapien. Sed ac risus. Phasellus lacinia, magna a ullamcorper laoreet, lectus arcu pulvinar risus, vitae facilisis libero dolor a purus. Sed vel lacus. Mauris nibh felis, adipiscing varius, adipiscing in, lacinia vel, tellus. Suspendisse ac urna. Etiam pellentesque mauris ut lectus. Nunc tellus ante, mattis eget, gravida vitae, ultricies ac, leo. Integer leo pede</p>

<div class="rule" style="left:189px;top:826px;width:822px"></div>

<h2 class="section-title" style="left:202px;top:858px">OUR BLOG</h2>
<div class="blog-avatar" style="top:909px" role="img" aria-label="Blog author portrait"></div>
<p class="blog-text" style="top:910px">In ultricies pellentesque massa a porta. Aliquam ipsum enim, hendrerit ut porta nec, ullamcorper et nulla. In eget mi dui, sit amet.</p>
<div class="rule" style="left:190px;top:972px;width:287px"></div>
<div class="blog-avatar" style="top:984px" role="img" aria-label="Blog author portrait"></div>
<p class="blog-text" style="top:985px">In ultricies pellentesque massa a porta. Aliquam ipsum enim, hendrerit ut porta nec, ullamcorper et nulla. In eget mi dui, sit amet.</p>
<div class="rule" style="left:190px;top:1046px;width:287px"></div>
<div class="blog-avatar" style="top:1058px" role="img" aria-label="Blog author portrait"></div>
<p class="blog-text" style="top:1059px">In ultricies pellentesque massa a porta. Aliquam ipsum enim, hendrerit ut porta nec, ullamcorper et nulla. In eget mi dui, sit amet.</p>

<h2 class="section-title" style="left:581px;top:858px">LATEST VIDEOS</h2>
<div class="ph video-main" role="img" aria-label="Video still of hikers with backpacks in a snowy forest"></div>
<div class="video-bar"></div>
<div class="ph video-thumb" role="img" aria-label="Video still of a paraglider over the sea" style="top:913px;height:86px;background:linear-gradient(180deg,#6fa9df,#a8cdee 60%,#5d87b0)"><span class="play" style="left:56px;top:32px"></span></div>
<div class="ph video-thumb" role="img" aria-label="Video still of skiers in goggles on a slope" style="top:1006px;height:83px;background:linear-gradient(160deg,#dfe8f1,#9fb2c6 60%,#6a7f93)"><span class="play" style="left:56px;top:30px"></span></div>
<a class="view-more">View More</a>

<div class="tab active" style="left:190px;width:107px">POETRY</div>
<div class="tab" style="left:303px;width:117px">PHOTOGRAPHY</div>
<div class="tab" style="left:428px;width:116px">AUDIO</div>
<div class="tab" style="left:553px;width:118px">ANIMATION</div>
<div class="tab-panel"></div>
<div class="ph" role="img" aria-label="Couple riding a sled down a snowy hill" style="left:190px;top:1274px;width:366px;height:190px;background:linear-gradient(170deg,#c9d9ea,#f2f4f7 55%,#e5e8ec)"></div>
<h3 class="tab-heading">INTEGER VITAE LIBERO AC RISUS</h3>
<div class="rule" style="left:581px;top:1311px;width:389px;background:#c9c9c9"></div>
<p class="tab-copy">Morbi interdum mollis sapien. Sed ac risus. Phasellus lacinia, magna a ullamcorper laoreet, lectus arcu pulvinar risus, vitae facilisis libero dolor a purus. Sed vel lacus. Mauris nibh felis, adipiscing varius, adipiscing in, lacinia vel, tellus. Suspendisse ac urna. Etiam pellentesque mauris ut lectus. Nunc tellus ante, mattis eget, gravida vitae, ultricies ac, leo. Integer leo pede</p>
<div class="readmore">READMORE
  <svg width="8" height="10" viewBox="0 0 8 10"><path d="M1 1l5 4-5 4" fill="none" stroke="#222" stroke-width="2"/></svg>
</div>

<h2 class="section-title" style="left:0;top:1535px;width:1200px;text-align:center">OUR LATEST PROJECTS</h2>
<div class="project" style="left:190px">
  <div class="project-img" role="img" aria-label="Woman stretching her arms by the sea" style="background:linear-gradient(180deg,#9fcbe8,#d9b48f 55%,#c8d35a)"></div>
  <div class="project-name">Lorem Ipsum</div><div class="project-sub">Simply test</div>
</div>
<div class="project" style="left:399px">
  <div class="project-img" role="img" aria-label="Golfer in blue shirt mid swing" style="background:linear-gradient(180deg,#7fb8df,#2a5fc4 55%,#7aa255)"></div>
  <div class="project-name">Bonorum et Malorum</div><div class="project-sub">Simply test</div>
</div>
<div class="project" style="left:608px">
  <div class="project-img" role="img" aria-label="Smiling woman stretching outdoors" style="background:linear-gradient(135deg,#8fd36a,#e9cfb7 50%,#2e5f8f)"></div>
  <div class="project-name">Injected humour</div><div class="project-sub">Simply test</div>
</div>
<div class="project" style="left:817px">
  <div class="project-img" role="img" aria-label="Two anglers fishing from a boat" style="background:linear-gradient(180deg,#eef1f5,#d9dde3 60%,#5a4a4a);border:1px solid #e3e3e3"></div>
  <div class="project-name">Embarrassing</div><div class="project-sub">Simply test</div>
</div>

<div class="rule" style="left:189px;top:1912px;width:822px"></div>
<h2 class="testi-title">CLIENT <b>TESTIMONIALS</b></h2>
<p class="testi-quote">Lorem Ipsum is simply dummy text of the printing and typesetting industry. Lorem Ipsum has been the industry's standard dummy text ever since type specimen book !!</p>
<svg class="abs" style="left:480px;top:2052px" width="240" height="12" viewBox="0 0 240 12">
  <path d="M0 1H112L120 9L128 1H240" fill="none" stroke="#d5d5d5" stroke-width="1"/>
</svg>
<p class="testi-name"><b>Tobin Vasker</b>, Company Name</p>
<span class="t-dot active" style="left:563px"></span>
<span class="t-dot" style="left:580px"></span>
<span class="t-dot" style="left:597px"></span>
<span class="t-dot" style="left:614px"></span>
<span class="t-dot" style="left:631px"></span>

<footer class="site-footer"></footer>
<div class="foot-col" style="left:189px;width:185px">
  <h4>COPPER LANTERN FILMS</h4>
  <p>There are many variations of passages of Lorem Ipsum available, but the majority have suffered alteration in some form, by injected humour, or randomised words which don't look even slightly believable. If you are going to use a passage of Lorem Ipsum, you need</p>
</div>
<div class="foot-col" style="left:406px;width:185px">
  <h4>CONTACT</h4>
  <p>There are many variations of passages of Lorem Ipsum available, but the majority have suffered alteration in so</p>
  <div class="contact-row"><svg width="12" height="14" viewBox="0 0 12 14"><path d="M6 0a5 5 0 0 0-5 5c0 4 5 9 5 9s5-5 5-9a5 5 0 0 0-5-5z" fill="#fff"/><circle cx="6" cy="5" r="2" fill="#b30000"/></svg>Adress</div>
  <div class="contact-row"><svg width="13" height="10" viewBox="0 0 13 10"><rect width="13" height="10" fill="#fff"/><path d="M0 0l6.5 5L13 0" fill="none" stroke="#b30000" stroke-width="1.2"/></svg>info@copperlanternfilms.com</div>
  <div class="contact-row"><svg width="12" height="12" viewBox="0 0 12 12"><path d="M2 0l3 3-1.5 2a8 8 0 0 0 3.5 3.5L9 7l3 3-2 2C5 12 0 7 0 2z" fill="#fff"/></svg>555-01472-88310</div>
</div>
<div class="foot-col" style="left:612px;width:200px">
  <h4>LATEST TWEETS</h4>
  <div class="tweet"><span class="tweet-dot"></span><div>Lorem Ipsum is simply dummy text of the printing and typesetting industry. Lorem Ipsum has been the industry's standard dummy</div></div>
  <div style="font-size:10.5px;margin:4px 0 6px 22px">1 Hour Ago</div>
  <div class="tweet"><span class="tweet-dot"></span><div>Lorem Ipsum is simply dummy text of the printing and typesetting</div></div>
  <div style="font-size:10.5px;margin:4px 0 0 22px">1 Hour Ago</div>
</div>
<div class="foot-col" style="left:848px;width:165px">
  <h4>NEWS LETTER</h4>
  <p>Type your email address below and recive our daily news letter for free</p>
</div>
<div class="email-field">Email Address</div>
<div class="email-go">GO</div>

<div class="bottom-bar"></div>
<p class="copyright">©Copy right &nbsp;2014 &nbsp;Copper Lantern Films &nbsp;| All rights reserved.</p>
<span class="social" style="left:928px"></span>
<span class="social" style="left:957px"></span>
<span class="social" style="left:986px"></span>

</body>
</html>
```